Marrowby Water Taxi and Transport Business Card

I need business cards for my new water taxi and freight transport business I have started here in Marrowby Alaska. Marrowby is a remote island in the middle of the gulf of Alaska. There are seven native villages around the island and Marrowby is the #2 fishing port in the United States. We also have the largest Coast Guard Base in the U.S. My company will be providing water taxi and freight transport logistics to the villages and many hunting and fishing lodges as well as remote properties around the island.

I would like a business card that isn't status quo, something that stands out, either in feel or appearance. I do like clean minimal designs but it needs to have the necessary contact info on it.

Target Market(s)

remote lodge / property owners, residents of the many villages around Marrowby and any one wanting to enjoy the great outdoors of Marrowby Alaska

Industry/Entity Type

Business

Contact Information for Business Card

I like clean simple designs that aren't cluttered but still provide the necessary information

Colors
0255a3
3277b5
33a4d5
9bcb3c
add136
fbed22
ffc214
f78f20
f37122

Requirements
Must have
• logo and contact info
• Captain Mason Elwick
• www.marrowbyferryline.com
• mason@marrowbyferryline.com

```html
<!DOCTYPE html>
<html lang="en">
<head>
<meta charset="utf-8">
<title>Marrowby Water Taxi and Transport – Business Card</title>
<link rel="stylesheet" href="https://fonts.googleapis.com/css2?family=Open+Sans:wght@400;700&display=swap">
<style>
  :root {
    --navy: #0255a3;
    --mid-blue: #3277b5;
    --sky: #33a4d5;
    --deep: #0a3f86;
    --white: #ffffff;
    --sun: #f78f20;
    --page: #e9ecef;
    --card-shadow: rgba(10, 30, 60, 0.22);
  }
  html, body {
    margin: 0;
    width: 1200px;
    height: 913px;
    overflow: hidden;
    background: var(--page);
    font-family: "Open Sans", Arial, sans-serif;
  }
  .sheet {
    position: relative;
    width: 1200px;
    height: 913px;
  }
  .card {
    position: absolute;
    top: 302px;
    width: 540px;
    height: 309px;
    border-radius: 16px;
    overflow: hidden;
    box-shadow: 0 10px 28px var(--card-shadow);
  }
  .card-front {
    left: 40px;
    background: linear-gradient(160deg, var(--deep) 0%, var(--navy) 40%, var(--sky) 100%);
  }
  .card-back {
    left: 620px;
    background: var(--white);
  }
  .front-art { position: absolute; inset: 0; }
  .brand {
    position: absolute;
    left: 62px;
    top: 34px;
    color: var(--white);
    font-weight: 700;
    display: flex;
    align-items: center;
    gap: 12px;
  }
  .brand-dot {
    width: 26px;
    height: 26px;
    border-radius: 50%;
    background: var(--sun);
    flex: none;
  }
  .brand-name { font-size: 34px; line-height: 1; letter-spacing: 1px; }
  .brand-line { font-size: 13px; line-height: 1.3; margin-top: 4px; letter-spacing: 0.5px; }
  .captain {
    position: absolute;
    right: 18px;
    top: 109px;
    font-size: 21px;
    font-weight: 700;
    color: var(--navy);
    margin: 0;
  }
  .contact {
    position: absolute;
    left: 26px;
    bottom: 26px;
    margin: 0;
    padding: 0;
    list-style: none;
    color: var(--white);
    font-size: 14px;
  }
  .contact li { display: flex; align-items: center; gap: 10px; margin-top: 4px; }
  .contact svg { width: 14px; height: 14px; flex: none; }
  .side-strip {
    position: absolute;
    left: 0; top: 0; bottom: 0;
    width: 40px;
    display: flex;
    flex-direction: column;
  }
  .side-strip span { flex: 1; }
  .side-strip span:nth-child(1) { background: var(--navy); }
  .side-strip span:nth-child(2) { background: var(--sky); }
  .side-strip span:nth-child(3) { background: var(--deep); }
  .side-strip span:nth-child(4) { background: var(--mid-blue); }
  .back-brand {
    position: absolute;
    left: 40px; right: 0; top: 0; bottom: 0;
    display: flex;
    align-items: center;
    justify-content: center;
    gap: 14px;
    color: var(--sky);
    font-weight: 700;
    font-size: 40px;
    letter-spacing: 1px;
  }
  .back-brand .brand-dot { width: 34px; height: 34px; }
</style>
</head>
<body>
<main class="sheet">
  <section class="card card-front" aria-label="Card front">
    <svg class="front-art" viewBox="0 0 540 309" aria-hidden="true">
      <polygon points="540,102 312,102 280,146 0,146 0,153 284,153 316,140 540,140" fill="#ffffff"/>
    </svg>
    <div class="brand">
      <span class="brand-dot"></span>
      <div>
        <div class="brand-name">Marrowby</div>
        <div class="brand-line">Water Taxi and Transport</div>
      </div>
    </div>
    <p class="captain">Captain Mason Elwick</p>
    <ul class="contact">
      <li>
        <svg viewBox="0 0 14 14"><rect x="1" y="3" width="12" height="8" rx="1" fill="none" stroke="#f78f20" stroke-width="1.5"/><path d="M1.5 3.5 7 8 12.5 3.5" fill="none" stroke="#f78f20" stroke-width="1.5"/></svg>
        mason@marrowbyferryline.com
      </li>
      <li>
        <svg viewBox="0 0 14 14"><circle cx="7" cy="7" r="5.8" fill="none" stroke="#f78f20" stroke-width="1.5"/><ellipse cx="7" cy="7" rx="2.4" ry="5.8" fill="none" stroke="#f78f20" stroke-width="1.2"/><path d="M1.2 7h11.6" stroke="#f78f20" stroke-width="1.2"/></svg>
        www.marrowbyferryline.com
      </li>
    </ul>
  </section>

  <section class="card card-back" aria-label="Card back">
    <div class="side-strip"><span></span><span></span><span></span><span></span></div>
    <div class="back-brand">
      <span class="brand-dot"></span>
      <span>Marrowby</span>
    </div>
  </section>
</main>
</body>
</html>
```